business card Calvanto

Wee need a business card design for a new compagny based on Paris
We developped innovative a platform for selling services to refresh, beautify and develop its housing.
We would like a red logo on a black background
Te final design should communicate quality service, know-how, high-end

Target Market(s)

individuals

Industry/Entity Type

Business

```html
<!DOCTYPE html>
<html lang="en">
<head>
<meta charset="utf-8">
<title>Calvanto — Business Card</title>
<link href="https://fonts.googleapis.com/css2?family=Montserrat:wght@700&family=Open+Sans:wght@400;600&display=swap" rel="stylesheet">
<style>
  :root {
    --backdrop: #d6d6d6;
    --card: #ffffff;
    --brand-red: #e05f5c;
    --ink: #2b2b2b;
    --wordmark-grey: #7a7a7a;
  }
  * { box-sizing: border-box; margin: 0; padding: 0; }
  html, body { width: 1200px; height: 852px; overflow: hidden; }
  body {
    background: var(--backdrop);
    font-family: "Open Sans", Arial, sans-serif;
    position: relative;
  }
  .card {
    position: absolute;
    top: 276px;
    width: 520px;
    height: 300px;
    background: var(--card);
    border-radius: 22px;
    box-shadow: 0 6px 16px rgba(0,0,0,0.18);
    overflow: hidden;
  }
  .card--front { left: 50px; }
  .card--back { left: 630px; }

  .brand {
    display: flex;
    align-items: center;
    gap: 14px;
  }
  .brand__mark {
    width: 52px;
    height: 52px;
    background: var(--brand-red);
  }
  .brand__name {
    font-family: "Open Sans", Arial, sans-serif;
    font-weight: 400;
    font-size: 50px;
    color: var(--wordmark-grey);
    letter-spacing: 0.5px;
    line-height: 1;
  }
  .card--front .brand {
    position: absolute;
    left: 50%;
    top: 50%;
    transform: translate(-50%, -50%);
  }

  .card--back .brand {
    position: absolute;
    right: -62px;
    top: 118px;
    transform: rotate(90deg);
    transform-origin: center;
  }
  .card--back .brand__mark { width: 42px; height: 42px; }
  .card--back .brand__name { font-size: 38px; }

  .holder {
    position: absolute;
    left: 38px;
    top: 56px;
  }
  .holder__name {
    font-family: "Montserrat", Arial, sans-serif;
    font-weight: 700;
    font-size: 20px;
    color: var(--brand-red);
  }
  .holder__role {
    font-size: 10.5px;
    font-weight: 600;
    color: var(--ink);
    margin-top: 2px;
  }

  .contact {
    position: absolute;
    left: 38px;
    bottom: 34px;
    list-style: none;
    font-size: 12.5px;
    color: var(--ink);
    font-weight: 600;
    line-height: 1.35;
  }
  .contact__item { display: flex; align-items: center; gap: 10px; }
  .contact__icon { width: 12px; height: 12px; fill: var(--brand-red); flex: none; }
  .contact__address { margin-top: 4px; }
</style>
</head>
<body>
  <section class="card card--front" aria-label="Card front">
    <div class="brand">
      <span class="brand__mark"></span>
      <span class="brand__name">Calvanto</span>
    </div>
  </section>

  <section class="card card--back" aria-label="Card back">
    <div class="holder">
      <p class="holder__name">Your Long Name</p>
      <p class="holder__role">Managing Director</p>
    </div>

    <ul class="contact">
      <li class="contact__item">
        <svg class="contact__icon" viewBox="0 0 12 12"><path d="M2 1h3l1 3-1.5 1a6 6 0 0 0 2.5 2.5L8 6l3 1v3a1 1 0 0 1-1 1A9 9 0 0 1 1 2a1 1 0 0 1 1-1z"/></svg>
        <span>00.00.00.0000</span>
      </li>
      <li class="contact__item">
        <svg class="contact__icon" viewBox="0 0 12 12"><path d="M3.5 0h5a1 1 0 0 1 1 1v10a1 1 0 0 1-1 1h-5a1 1 0 0 1-1-1V1a1 1 0 0 1 1-1zm0 1.5v8h5v-8z"/></svg>
        <span>00.00.00.0000</span>
      </li>
      <li class="contact__item">
        <svg class="contact__icon" viewBox="0 0 12 12"><path d="M0 2h12v8H0zM1 3v.4l5 3.2 5-3.2V3z"/></svg>
        <span>yourname@yourwebsite.com</span>
      </li>
      <li class="contact__item">
        <svg class="contact__icon" viewBox="0 0 12 12"><path d="M6 0a6 6 0 1 0 0 12A6 6 0 0 0 6 0zm0 1.2c.7.8 1.2 2 1.3 3.3H4.7C4.8 3.2 5.3 2 6 1.2zM1.3 5.5h2.4c.1 1.3.5 2.5 1.1 3.5A4.8 4.8 0 0 1 1.3 5.5zm0-1A4.8 4.8 0 0 1 4.8 1.2c-.6 1-1 2.1-1.1 3.3zm3.4 1h2.6c-.1 1.3-.6 2.5-1.3 3.3-.7-.8-1.2-2-1.3-3.3zm3.6 0h2.4a4.8 4.8 0 0 1-3.5 3.5c.6-1 1-2.2 1.1-3.5zm0-1c-.1-1.2-.5-2.3-1.1-3.3a4.8 4.8 0 0 1 3.5 3.3z"/></svg>
        <span>www.yourwebsite.com</span>
      </li>
      <li class="contact__address">Your Commercial or office address<br>in just two line with pincode</li>
    </ul>

    <div class="brand">
      <span class="brand__mark"></span>
      <span class="brand__name">Calvanto</span>
    </div>
  </section>
</body>
</html>
```